Marlowe Plumbing Heating and Electric

We are looking for a basic, but very beautiful and professional looking website. We would like the ability for a customer to request service through our website via a form or email that will be forwarded to us. Other then that just contact info, our history, our rates, and the services we offer.

Look at his page, it is WAY TOO BASIC, but if gives a very general base line idea: http://www.ringfastpiping.example/

http://www.pipewizard.example/norfolk/

http://www.dranbolt-williamsburg.example/emergency_plumbing.html

Target Market(s)

Heating, air conditioning, plumbing, natural gas

Industry/Entity Type

Plumbing

Number of Pages Required

4 page

Requirements
Must have
• Professional looking, very high end and modern,
Nice to have
• Would like the ability for client to contact us for service through the website utilizing some type of email.

```html
<!DOCTYPE html>
<html lang="en">
<head>
<meta charset="utf-8">
<title>Marlowe Plumbing Heating and Electric – Rates</title>
<link rel="stylesheet" href="https://fonts.googleapis.com/css2?family=Open+Sans:wght@400;700&family=Merriweather:wght@400&display=swap">
<style>
  :root {
    --bar: #2e2e2e;
    --accent: #2b9af3;
    --phone: #1f9fe0;
    --ink: #111111;
    --white: #ffffff;
    --social-a: #4a6398;
    --social-b: #ff6b4a;
    --social-c: #27bcf7;
  }
  * { box-sizing: border-box; margin: 0; padding: 0; }
  html, body { width: 1200px; height: 960px; overflow: hidden; background: var(--white); }
  body { position: relative; font-family: "Open Sans", Arial, sans-serif; color: var(--ink); }

  .site-header { position: absolute; top: 0; left: 0; width: 1200px; height: 94px; background: var(--bar); }
  .brand-name { position: absolute; left: 39px; top: 32px; font-weight: 400; font-size: 22px; line-height: 28px; color: var(--white); }
  .main-nav a { position: absolute; top: 35px; font-size: 20px; color: var(--white); text-decoration: none; }
  .main-nav a.is-current { color: var(--accent); }
  .header-phone { position: absolute; left: 1011px; top: 32px; font-size: 19px; color: var(--phone); }

  .rates { position: absolute; left: 39px; top: 0; width: 800px; }
  .rate-group { position: absolute; left: 0; width: 800px; }
  .rate-group h2 { font-weight: 400; font-size: 24px; color: var(--accent); line-height: 1; }
  .rate-group h2.serif { font-family: "Merriweather", Georgia, serif; }
  .rate-group ul { list-style: none; font-size: 13px; line-height: 15.8px; }

  .site-footer { position: absolute; top: 677px; left: 0; width: 1200px; height: 283px; background: var(--bar); }
  .footer-nav { position: absolute; left: 314px; top: 50px; display: flex; flex-direction: column; }
  .footer-nav a { color: var(--white); font-size: 16px; line-height: 17px; text-decoration: underline; }
  .social { position: absolute; top: 52px; width: 68px; height: 68px; box-shadow: 0 2px 4px rgba(0,0,0,.4); }
  .social-a { left: 482px; background: var(--social-a); }
  .social-b { left: 565px; background: var(--social-b); }
  .social-c { left: 653px; background: var(--social-c); }
  .footer-phone { position: absolute; left: 887px; top: 46px; font-size: 19px; color: var(--white); }
</style>
</head>
<body>
  <header class="site-header">
    <div class="brand-name">Marlowe Plumbing</div>
    <nav class="main-nav">
      <a href="#" style="left:390px">Home</a>
      <a href="#" style="left:495px">About us</a>
      <a href="#" class="is-current" style="left:621px">Rates</a>
      <a href="#" style="left:723px">Services</a>
    </nav>
    <div class="header-phone">(999)999-9999</div>
  </header>

  <main class="rates">
    <section class="rate-group" style="top:122px">
      <h2>Plumbing Prices</h2>
      <ul style="margin-top:16px">
        <li>Water Heater Installation/Replacement (40 gallon gas water heater) $825 - $1125</li>
        <li>Kitchen Faucet Installation (customer supplied faucet) $225 - $350</li>
        <li>Clogged Toilet $155 - $375 (possibly more if it is very bad mainline clog)</li>
        <li>Drain Cleaning (localized) $175 - $325</li>
        <li>Water Line Replacement (from the curb stop to the house) $2,500 - $8,000</li>
      </ul>
    </section>

    <section class="rate-group" style="top:275px">
      <h2 class="serif">Heating Prices</h2>
      <ul style="margin-top:17px">
        <li>Boiler, Furnace or Heat Pump Repairs (pricing all depends on what's actually wrong) $125 - $700</li>
        <li>Install mid-efficiency gas forced-air furnace $2,500 - $4,200</li>
        <li>Install high-efficiency gas forced-air furnace $3,500 - $5,500</li>
        <li>Install mid-efficiency gas boiler $3,800 - $5,800</li>
        <li>Install high-efficiency gas boiler $5,800 - $8,800</li>
        <li>Furnace Maintenance $125 - $225</li>
        <li>Boiler Maintenance $175 - $275</li>
      </ul>
    </section>

    <section class="rate-group" style="top:460px">
      <h2 class="serif">Electric Prices</h2>
      <ul style="margin-top:26px">
        <li>Boiler, Furnace or Heat Pump Repairs (pricing all depends on what's actually wrong) $125 - $700</li>
        <li>Install mid-efficiency gas forced-air furnace $2,500 - $4,200</li>
        <li>Install high-efficiency gas forced-air furnace $3,500 - $5,500</li>
        <li>Install mid-efficiency gas boiler $3,800 - $5,800</li>
        <li>Install high-efficiency gas boiler $5,800 - $8,800</li>
        <li>Furnace Maintenance $125 - $225</li>
        <li>Boiler Maintenance $175 - $275</li>
      </ul>
    </section>
  </main>

  <footer class="site-footer">
    <nav class="footer-nav">
      <a href="#">home</a>
      <a href="#">about us</a>
      <a href="#">rates</a>
      <a href="#">services</a>
    </nav>
    <a href="#" class="social social-a" aria-label="Social profile one"></a>
    <a href="#" class="social social-b" aria-label="Social profile two"></a>
    <a href="#" class="social social-c" aria-label="Social profile three"></a>
    <div class="footer-phone">(999)999-9999</div>
  </footer>
</body>
</html>
```